Oil Field Service company needs professional business cards

Looking to clean up our current company business cards and look a little more professional. Brenwick Casing Services is a US based company that services the oil field. We deal with engineers, managers and oil rigs....................................................................................................................................................................................................................................................................................................................................................................................................

Target Market(s)

Oil and Gas professionals

Industry/Entity Type

Oil And Gas

Contact Information for Business Card

See attached photo as example

Font styles to use
Sans Serif

Colors
ec1f27

Requirements
Must have
• Company Logo, Name, Title, Cell, Office, Fax, Email.
• See attached photo
Nice to have
• External CRT, Internal CRT, Casing Crews, Torque Turn, Laydown Machine
Should not have
• Do not introduce any new pictures and keep it professional looking

```html
<!DOCTYPE html>
<html lang="en">
<head>
<meta charset="utf-8">
<title>Brenwick Casing Services – Business Card</title>
<link rel="stylesheet" href="https://fonts.googleapis.com/css2?family=Open+Sans:wght@400;600;700;800&display=swap">
<style>
  :root {
    --brand-red: #ec1f27;
    --slate: #3f4750;
    --ink: #2d3239;
    --card-white: #ffffff;
    --backdrop: #2b2d31;
  }
  * { margin: 0; padding: 0; box-sizing: border-box; }
  html, body {
    width: 1200px; height: 864px; overflow: hidden;
    background: var(--backdrop);
    font-family: "Open Sans", Arial, sans-serif;
  }
  .stage {
    position: relative; width: 1200px; height: 864px;
  }
  .card {
    position: absolute; left: 320px;
    width: 560px; height: 320px;
    overflow: hidden;
  }
  .card--front { top: 88px; background: var(--brand-red); }
  .card--back  { top: 456px; background: var(--card-white); }

  /* Front */
  .front-wordmark {
    position: absolute; inset: 0;
    display: flex; flex-direction: column; align-items: center; justify-content: center;
    color: var(--card-white); font-weight: 800; text-align: center;
  }
  .front-wordmark .name-main { font-size: 44px; letter-spacing: 4px; line-height: 1; }
  .front-wordmark .name-sub { font-size: 15px; letter-spacing: 4px; margin-top: 10px; }

  /* Back */
  .back-wordmark {
    position: absolute; right: 34px; top: 62px;
    color: var(--slate); font-weight: 800; text-align: center;
  }
  .back-wordmark .name-main { font-size: 40px; letter-spacing: 4px; line-height: 1; }
  .back-wordmark .name-sub { font-size: 14px; letter-spacing: 4px; margin-top: 8px; }

  .holder { position: absolute; left: 34px; top: 100px; }
  .holder-name { color: var(--brand-red); font-weight: 700; font-size: 15px; }
  .holder-title { color: var(--ink); font-size: 13px; margin-top: 2px; }

  .divider {
    position: absolute; left: 0; right: 0; top: 146px;
    height: 2px; background: var(--brand-red);
  }

  .contacts {
    position: absolute; left: 196px; top: 172px;
    list-style: none; color: var(--ink); font-size: 14px; line-height: 19px;
  }
  .contacts li { display: flex; align-items: center; gap: 8px; }
  .contacts svg { width: 11px; height: 11px; fill: var(--brand-red); flex: none; }

  .services {
    position: absolute; left: 0; right: 0; top: 262px;
    text-align: center; color: var(--ink); font-size: 14.5px;
  }
</style>
</head>
<body>
<main class="stage">
  <section class="card card--front" aria-label="Business card front">
    <div class="front-wordmark">
      <span class="name-main">BRENWICK</span>
      <span class="name-sub">CASING SERVICES</span>
    </div>
  </section>

  <section class="card card--back" aria-label="Business card back">
    <div class="holder">
      <p class="holder-name">Cody Hallbrook</p>
      <p class="holder-title">Area Manager</p>
    </div>

    <div class="back-wordmark">
      <div class="name-main">BRENWICK</div>
      <div class="name-sub">CASING SERVICES</div>
    </div>

    <div class="divider"></div>

    <ul class="contacts">
      <li>
        <svg viewBox="0 0 24 24" aria-hidden="true"><path d="M6.6 10.8a15.1 15.1 0 0 0 6.6 6.6l2.2-2.2c.3-.3.7-.4 1-.2 1.1.4 2.3.6 3.6.6.6 0 1 .4 1 1V20c0 .6-.4 1-1 1A17 17 0 0 1 3 4c0-.6.4-1 1-1h3.5c.6 0 1 .4 1 1 0 1.3.2 2.5.6 3.6.1.3 0 .7-.2 1z"/></svg>
        (555) 410-2200
      </li>
      <li>
        <svg viewBox="0 0 24 24" aria-hidden="true"><path d="M7 1h10a2 2 0 0 1 2 2v18a2 2 0 0 1-2 2H7a2 2 0 0 1-2-2V3a2 2 0 0 1 2-2zm0 3v14h10V4zm5 15.2a1.2 1.2 0 1 0 0 2.4 1.2 1.2 0 0 0 0-2.4z"/></svg>
        (555) 418-6631
      </li>
      <li>
        <svg viewBox="0 0 24 24" aria-hidden="true"><path d="M6 2h9l3 3v4h1a3 3 0 0 1 3 3v8a2 2 0 0 1-2 2H4a2 2 0 0 1-2-2v-8a3 3 0 0 1 3-3h1zm2 2v5h8V6h-3V4zm-1 9v2h3v-2zm5 0v2h3v-2zm-5 4v2h3v-2zm5 0v2h3v-2z"/></svg>
        (555) 410-2290
      </li>
      <li>
        <svg viewBox="0 0 24 24" aria-hidden="true"><path d="M2 5h20v14H2zm2 2v.5l8 5.5 8-5.5V7zm0 2.9V17h16V9.9l-8 5.5z"/></svg>
        cody.hallbrook@example.com
      </li>
    </ul>

    <p class="services">Laydown Machine | Casing Crew | Mud Tool | Torque Turn</p>
  </section>
</main>
</body>
</html>
```